Email Marketing Campaign 50% discount and buy-2-get-1 offer

I would like to inform my customers of our special offers via a e-Newsletter/Marketing E-Mail.

The coding needs to be done by the designer.

I have most of the design and the message that we wish to convey our buyers.

The information is:

1. We have now 50% discount on all our carpets

2. We have a buy-2 get-1 free carpet offer

For both the above messages we have already banner style that we like to use in our Newsletter.
I have attached the banner and the designers can use it.

3. We have opened a new shop in Berlin Germany

Therefore we like to have a Sylish Newsletter design that fits our website and products using the banner idea and we wish to include the 3 messages.
Special note should be given that this newsletter is going to our previous buyers. Therefore they already know us, and we just like to inform them of our latest news and offer.

Target Market(s)

Upmarket buyers looking for a great deal

Industry/Entity Type

Marketing

Coding

Coded - Design and coding required

Number of Pages Required

1 page

Font styles to use
Sans Serif

Colors
e667a6
34a7d8

Requirements
Must have
• Clear explanation with excitement in the message
Nice to have
• To promote clearly the 3 for 2 with maybe an explanation and clear images describing what the promotion is and how it works.
• I.e. buy 2 get 1 extra carpet of your choice free
• Add carpets to checkout and the system will calculate automatically
• The lowest carpet in your selection of 3 is the free carpet

```html
<!DOCTYPE html>
<html lang="en">
<head>
<meta charset="utf-8">
<title>Buy 2 Get 1 Free – Carpet Offer</title>
<link rel="stylesheet" href="https://fonts.googleapis.com/css2?family=Lato:wght@400;700&family=Raleway:wght@300;400;500;600;700&display=swap">
<style>
  :root {
    --page-bg: #fafafa;
    --band-bg: #ffffff;
    --ink: #000000;
    --paper: #ffffff;
    --text-dark: #2b2b2b;
    --text-soft: #666666;
    --offer-blue: #5b9bd5;
    --frame-blue: #7fa7c9;
    --brand-pink: #e667a6;
    --brand-blue: #34a7d8;
    --rug-red: #a3121a;
    --rug-edge: #d9c18e;
  }
  * { box-sizing: border-box; margin: 0; padding: 0; }
  html, body { width: 1200px; height: 722px; overflow: hidden; background: var(--page-bg); }
  .canvas { position: relative; width: 1200px; height: 722px; background: var(--page-bg); }

  /* Offer badge */
  .offer-badge {
    position: absolute; left: 483px; top: 22px; width: 266px; height: 99px;
    border: 1px solid var(--frame-blue); background: var(--paper); padding: 3px 4px 4px 4px;
    display: flex; font-family: "Lato", sans-serif; color: var(--paper);
  }
  .offer-badge__deal { width: 93px; display: flex; flex-direction: column; background: var(--ink); }
  .offer-badge__line {
    flex: 1; display: flex; align-items: center; justify-content: center;
    font-size: 21px; font-weight: 700; letter-spacing: 0.3px;
  }
  .offer-badge__line + .offer-badge__line { border-top: 1px solid #555; }
  .offer-badge__reward {
    flex: 1; background: var(--offer-blue); display: flex; flex-direction: column;
    align-items: center; justify-content: center; line-height: 1;
  }
  .offer-badge__free { font-size: 54px; font-weight: 700; letter-spacing: 1px; margin-top: -4px; }
  .offer-badge__extra { font-size: 12px; font-weight: 700; margin-top: 3px; }
  .offer-badge__shipping { font-size: 13px; letter-spacing: 1.6px; margin-top: 2px; }

  /* Banner band */
  .banner-band { position: absolute; left: 0; top: 142px; width: 1200px; height: 472px; background: var(--band-bg); }
  .banner { position: absolute; left: 54px; top: 0; width: 1090px; height: 472px; overflow: hidden; }
  .banner__art { position: absolute; inset: 0; }
  .banner__text {
    position: absolute; font-family: "Raleway", sans-serif; color: var(--paper);
    text-align: center; white-space: nowrap; line-height: 1; transform: translateX(-50%);
  }
  .buy-one { left: 153px; top: 137px; font-size: 47px; font-weight: 600; letter-spacing: 0.5px; }
  .get-off { left: 159px; top: 291px; font-size: 39px; font-weight: 600; }
  .get-off .percent { font-size: 60px; font-weight: 300; }
  .buy-two { left: 935px; top: 103px; font-size: 39px; font-weight: 600; }
  .with-off { left: 937px; top: 237px; font-size: 35px; font-weight: 600; }
  .with-off strong { font-weight: 700; }
  .get-one { left: 937px; top: 278px; font-size: 35px; font-weight: 600; }
  .free-word { left: 831px; top: 336px; font-size: 35px; font-weight: 600; }

  .rug {
    position: absolute; background: var(--rug-red);
    border: 4px solid var(--rug-edge); box-shadow: 0 2px 4px rgba(0,0,0,0.4);
  }
  .rug--single { left: 90px; top: 196px; width: 138px; height: 73px; }
  .rug--pair-a { left: 865px; top: 157px; width: 90px; height: 50px; }
  .rug--pair-b { left: 918px; top: 167px; width: 100px; height: 52px; }
  .rug--free { left: 888px; top: 319px; width: 140px; height: 73px; }

  /* News strip */
  .news-strip {
    position: absolute; left: 54px; top: 630px; width: 1090px; height: 78px;
    display: flex; gap: 20px; font-family: "Raleway", sans-serif;
  }
  .news-item {
    flex: 1; display: flex; align-items: center; gap: 18px;
    background: var(--paper); padding: 0 22px; border-left: 6px solid var(--brand-pink);
  }
  .news-item--shop { border-left-color: var(--brand-blue); }
  .news-item__tag {
    font-size: 30px; font-weight: 700; color: var(--brand-pink); white-space: nowrap; line-height: 1;
  }
  .news-item--shop .news-item__tag { color: var(--brand-blue); }
  .news-item__copy { line-height: 1.3; }
  .news-item__title { font-size: 17px; font-weight: 700; color: var(--text-dark); }
  .news-item__note { font-size: 14px; font-weight: 400; color: var(--text-soft); }
</style>
</head>
<body>
<main class="canvas">
  <section class="offer-badge" aria-label="Buy 2 get 1 free offer">
    <div class="offer-badge__deal">
      <span class="offer-badge__line">BUY 2</span>
      <span class="offer-badge__line">GET 1</span>
    </div>
    <div class="offer-badge__reward">
      <span class="offer-badge__free">FREE</span>
      <span class="offer-badge__extra">+40% EXTRA DISCOUNT</span>
      <span class="offer-badge__shipping">+ FREE SHIPPING</span>
    </div>
  </section>

  <section class="banner-band">
    <div class="banner">
      <svg class="banner__art" width="1090" height="472" viewBox="0 0 1090 472">
        <defs>
          <linearGradient id="roomTone" x1="0" y1="0" x2="0" y2="1">
            <stop offset="0" stop-color="#efe3c4"/>
            <stop offset="0.6" stop-color="#e2cfa3"/>
            <stop offset="0.72" stop-color="#c98a45"/>
            <stop offset="1" stop-color="#d9b230"/>
          </linearGradient>
          <linearGradient id="bokehLeft" x1="0" y1="0" x2="1" y2="0">
            <stop offset="0" stop-color="#5a3a1c"/>
            <stop offset="0.35" stop-color="#7a5a2a"/>
            <stop offset="0.7" stop-color="#2f5a22"/>
            <stop offset="1" stop-color="#4d6b30"/>
          </linearGradient>
          <linearGradient id="bokehRight" x1="0" y1="0" x2="1" y2="0">
            <stop offset="0" stop-color="#5a3a1c"/>
            <stop offset="0.4" stop-color="#3d5a22"/>
            <stop offset="0.75" stop-color="#2a3a18"/>
            <stop offset="1" stop-color="#1e2410"/>
          </linearGradient>
        </defs>
        <rect width="1090" height="472" fill="url(#roomTone)" role="img" aria-label="Living room with fireplace and a yellow overdyed carpet on the floor"/>
        <polygon points="0,0 362,0 296,472 0,472" fill="url(#bokehLeft)" role="img" aria-label="Warm blurred festive lights background"/>
        <polygon points="795,0 1090,0 1090,472 729,472" fill="url(#bokehRight)" role="img" aria-label="Warm blurred festive lights background"/>
      </svg>

      <p class="banner__text buy-one">BUY ONE</p>
      <div class="rug rug--single" role="img" aria-label="Red kilim rug"></div>
      <p class="banner__text get-off">GET <span class="percent">40%</span> OFF</p>

      <p class="banner__text buy-two">BUY TWO</p>
      <div class="rug rug--pair-a" role="img" aria-label="Red kilim rug"></div>
      <div class="rug rug--pair-b" role="img" aria-label="Red kilim rug"></div>
      <p class="banner__text with-off">WITH <strong>40%</strong> OFF</p>
      <p class="banner__text get-one">AND GET ONE</p>
      <p class="banner__text free-word">FREE</p>
      <div class="rug rug--free" role="img" aria-label="Red kilim rug"></div>
    </div>
  </section>

  <section class="news-strip" aria-label="Latest news">
    <article class="news-item news-item--sale">
      <span class="news-item__tag">50% OFF</span>
      <div class="news-item__copy">
        <p class="news-item__title">Half price on all our carpets</p>
        <p class="news-item__note">The cheapest of any 3 carpets is free at checkout</p>
      </div>
    </article>
    <article class="news-item news-item--shop">
      <span class="news-item__tag">BERLIN</span>
      <div class="news-item__copy">
        <p class="news-item__title">Our new shop is now open in Berlin</p>
        <p class="news-item__note">Come and see the full collection in person</p>
      </div>
    </article>
  </section>
</main>
</body>
</html>
```